New business card/stationary for a consulting company

I am looking for a clean and very professional looking business card for my consulting company as well as corresponding stationary. I am uploading our logo. I like simple and powerful for the feel. No graphics but I am open on everything else. Below is my contact information but would like the final to be in a version I can add my employees information into and print. Thank you.

Daniel Whitcombe
dan@ferncliffadvisory.com
2870 North 9th Avenue, Summit Floor, Elm Ridge, Illinois 60531
www.ferncliffadvisory.com

Industry/Entity Type

Consulting

Contact Information for Business Card

Daniel Whitcombe
dan@ferncliffadvisory.com
www.ferncliffadvisory.com

Font styles to use
Serif
Sans Serif

Requirements
Must have
• Our logo and the business card details.
Nice to have
• our website www.ferncliffadvisory.com

```html
<!DOCTYPE html>
<html lang="en">
<head>
<meta charset="utf-8">
<title>Ferncliff Advisory — Business Card</title>
<link rel="stylesheet" href="https://fonts.googleapis.com/css2?family=Open+Sans:wght@300;400;700&display=swap">
<style>
  :root {
    --navy: #0b0a78;
    --navy-deep: #06055a;
    --royal: #1c17c9;
    --paper: #f7f7f9;
    --white: #ffffff;
    --backdrop: #2b2c30;
  }
  * { box-sizing: border-box; margin: 0; padding: 0; }
  html, body {
    width: 1200px; height: 900px; overflow: hidden;
    background: var(--backdrop);
    font-family: "Open Sans", Arial, sans-serif;
  }
  .canvas {
    position: relative; width: 1200px; height: 900px;
  }
  .card {
    position: absolute; left: 250px; width: 700px; height: 400px;
    overflow: hidden;
    box-shadow: 0 10px 30px rgba(0,0,0,0.45);
  }
  .card--front {
    top: 36px;
    background: linear-gradient(100deg, var(--royal) 0%, #1412a8 45%, var(--navy-deep) 100%);
    color: var(--white);
  }
  .card--back {
    top: 464px;
    background: var(--paper);
  }

  .brand {
    position: absolute; left: 0; right: 0;
    display: flex; align-items: center; justify-content: center; gap: 18px;
  }
  .brand__square {
    width: 30px; height: 30px;
  }
  .brand__name {
    font-weight: 300; font-size: 36px; letter-spacing: 2px;
    text-transform: uppercase; white-space: nowrap;
  }
  .card--front .brand { top: 150px; }
  .card--front .brand__square { background: var(--white); }
  .card--front .brand__name { color: var(--white); }

  .front__web {
    position: absolute; left: 0; right: 0; bottom: 52px;
    text-align: center; font-size: 17px; font-weight: 400;
    letter-spacing: 7px; color: var(--white);
  }

  .card--back .brand { top: 92px; }
  .card--back .brand__square { background: var(--navy); }
  .card--back .brand__name { color: var(--navy); }

  .contact-band {
    position: absolute; left: 0; right: 0; top: 196px; height: 204px;
    background: linear-gradient(100deg, var(--navy) 0%, #15129a 60%, var(--navy) 100%);
    color: var(--white); text-align: center;
  }
  .contact-band__rule {
    position: absolute; left: 0; right: 0; height: 3px; background: var(--white);
  }
  .contact-band__rule--top { top: 8px; }
  .contact-band__rule--bottom { bottom: 22px; }
  .contact-band__details { padding-top: 38px; }
  .contact__name {
    font-weight: 700; font-size: 21px; letter-spacing: 0.5px;
    text-transform: uppercase; margin-bottom: 8px;
  }
  .contact__line { font-size: 15px; line-height: 24px; }
  .contact__label { font-weight: 700; }
  .contact__gap { display: inline-block; width: 14px; }
</style>
</head>
<body>
<main class="canvas">

  <section class="card card--front" aria-label="Card front">
    <div class="brand">
      <span class="brand__square"></span>
      <span class="brand__name">Ferncliff Advisory</span>
    </div>
    <p class="front__web">www.ferncliffadvisory.com</p>
  </section>

  <section class="card card--back" aria-label="Card back">
    <div class="brand">
      <span class="brand__square"></span>
      <span class="brand__name">Ferncliff Advisory</span>
    </div>
    <div class="contact-band">
      <span class="contact-band__rule contact-band__rule--top"></span>
      <div class="contact-band__details">
        <p class="contact__name">Daniel Whitcombe</p>
        <p class="contact__line">2870 North 9th Avenue, Summit Floor, Elm Ridge, Illinois 60531</p>
        <p class="contact__line">
          <span class="contact__label">E:</span> dan@ferncliffadvisory.com<span class="contact__gap"></span><span class="contact__label">W:</span> ferncliffadvisory.com
        </p>
      </div>
      <span class="contact-band__rule contact-band__rule--bottom"></span>
    </div>
  </section>

</main>
</body>
</html>
```